A6 Flyers for sports betting / sports advisory service

WE are looking for flyer design for our business to promote a new promo. The flyer must be in similar colours to our website www.kestrelvane.com.au.

the flyer must contain a small intro to who we are and what we do as well as details of how to subscribe to our website etc. It must be eye catching as these will be given out to potential customers as sporting events etc

Target Market(s)

Sports Bettors / Gamblers

Industry/Entity Type

Gambling

Font styles to use
Serif

Requirements
Must have
• Catchy look and layout in colours similar to our website
Nice to have
• scan code
Should not have
• None

```html
<!DOCTYPE html>
<html lang="en">
<head>
<meta charset="utf-8">
<title>Kestrel Vane – A6 Flyer</title>
<link rel="stylesheet" href="https://fonts.googleapis.com/css2?family=Montserrat:wght@500;700;800&family=Raleway:wght@300;400;600&display=swap">
<style>
  :root {
    --canvas: #efefef;
    --paper: #ffffff;
    --ink: #0d0d0d;
    --black: #111111;
    --green: #74970f;
    --green-bright: #8dbb13;
    --grass: #3f6a12;
    --grey: #6b6b6b;
    --white: #ffffff;
  }
  * { box-sizing: border-box; margin: 0; padding: 0; }
  html, body { width: 1200px; height: 800px; overflow: hidden; }
  body {
    background: var(--canvas);
    font-family: "Raleway", sans-serif;
    position: relative;
  }
  .flyer {
    position: absolute;
    top: 46px;
    width: 500px;
    height: 708px;
    background: var(--black);
    overflow: hidden;
    box-shadow: 0 12px 30px rgba(0,0,0,.18);
  }
  .flyer--front { left: 70px; }
  .flyer--back { left: 630px; }

  /* brand mark */
  .brand {
    display: flex;
    align-items: center;
    gap: 10px;
    font-family: "Montserrat", sans-serif;
    font-weight: 700;
    color: var(--green);
  }
  .brand__square { width: 22px; height: 22px; background: var(--grey); }

  /* front */
  .front__head {
    position: absolute; inset: 0 0 auto 0; height: 240px;
    background: var(--paper);
    padding: 36px 40px 0;
    z-index: 2;
  }
  .front__head .brand { font-size: 26px; }
  .headline {
    margin-top: 34px;
    font-family: "Montserrat", sans-serif;
    font-weight: 800;
    line-height: 1;
    text-transform: uppercase;
    white-space: nowrap;
  }
  .headline__name { color: var(--ink); font-size: 32px; display: block; }
  .headline__tag { color: var(--green); font-size: 32px; display: block; margin-top: 8px; }
  .front__photo {
    position: absolute; left: 0; right: 0; top: 240px; height: 240px;
    background:
      radial-gradient(circle at 70% 20%, rgba(255,255,255,.7), transparent 18%),
      linear-gradient(180deg, #9a9ea4 0%, #585c60 45%, #3b5f16 80%, var(--black) 100%);
    z-index: 1;
  }
  .front__grass, .back__grass {
    position: absolute; right: 0; bottom: 0; width: 320px; height: 300px;
    background: radial-gradient(ellipse at 100% 100%, var(--green-bright) 0%, var(--grass) 35%, transparent 72%);
    opacity: .75;
  }
  .front__foot {
    position: absolute; left: 0; right: 0; bottom: 22px;
    display: flex; flex-direction: column; align-items: center; gap: 20px;
    z-index: 3;
  }
  .info-panel {
    position: relative;
    width: 430px;
    background: var(--green);
    color: var(--white);
    padding: 20px 24px;
    text-align: center;
    font-size: 11.5px;
    line-height: 1.45;
    font-weight: 400;
  }
  .info-panel p + p { margin-top: 10px; }
  .info-panel__tab {
    position: absolute; top: 50%; width: 14px; height: 60px; margin-top: -30px; background: var(--grey);
  }
  .info-panel__tab--left { left: -14px; }
  .info-panel__tab--right { right: -14px; }
  .divider { display: block; width: 120px; height: 2px; background: var(--white); }
  .site-url {
    font-family: "Montserrat", sans-serif;
    font-weight: 700;
    font-size: 22px;
    color: var(--white);
    text-align: center;
  }
  .flyer--back .site-url {
    position: absolute; left: 0; right: 0; bottom: 22px; z-index: 3;
  }

  /* back */
  .back__head {
    position: absolute; inset: 0 0 auto 0; height: 170px;
    background: linear-gradient(180deg, var(--paper) 80%, rgba(255,255,255,0));
    display: flex; align-items: center; justify-content: center;
    z-index: 2;
  }
  .back__head .brand { font-size: 30px; }
  .back__body {
    position: absolute; left: 40px; right: 40px; top: 200px;
    color: var(--white);
    font-size: 13px;
    line-height: 1.55;
    z-index: 3;
  }
  .back__body p + p { margin-top: 18px; }
  .highlight {
    display: block;
    color: var(--green-bright);
    font-family: "Montserrat", sans-serif;
    font-weight: 700;
    font-size: 20px;
  }
  .inline-highlight {
    color: var(--green-bright);
    font-family: "Montserrat", sans-serif;
    font-weight: 700;
    font-size: 18px;
  }
  .fine-print { font-size: 11px; opacity: .85; }
</style>
</head>
<body>

<section class="flyer flyer--front">
  <header class="front__head">
    <div class="brand"><span class="brand__square"></span>Kestrel Vane</div>
    <h1 class="headline">
      <span class="headline__name">Kestrel Vane</span>
      <span class="headline__tag">Your best bet yet!</span>
    </h1>
  </header>
  <div class="front__photo" role="img" aria-label="Floodlit stadium with a celebrating fan silhouetted against the pitch"></div>
  <div class="front__grass" role="img" aria-label="Lit grass pitch fading into black"></div>

  <div class="front__foot">
    <div class="info-panel">
      <span class="info-panel__tab info-panel__tab--left"></span>
      <span class="info-panel__tab info-panel__tab--right"></span>
      <p>"When you want daily sports tips and strategies that you can rely on, Kestrel Vane is the way to go every time. Our team of experienced sports betting analysts have access to a range of sports across the globe, and cater to punting fanatics anywhere in the world!</p>
      <p>When we say we're sports fanatics, we mean it. We live and breathe everything including basketball, soccer, football, rugby, cricket and more. We put hours and hours into researching and strategy before the game, so that you're equipped with well-informed daily sports tips."</p>
    </div>
    <span class="divider"></span>
    <p class="site-url">www.kestrelvane.com.au</p>
  </div>
</section>

<section class="flyer flyer--back">
  <header class="back__head">
    <div class="brand"><span class="brand__square"></span>Kestrel Vane</div>
  </header>
  <div class="back__grass" role="img" aria-label="Lit grass pitch fading into black"></div>
  <div class="back__body">
    <p>Kestrel Vane is a subscription based service which aims to provide profitable sports tips to our members. We are averaging a 64% win ratio across our proven systems for our punters!</p>
    <p>Join online at <span class="highlight">kestrelvane.com.au</span> or find us on our socials and see the results for yourself!</p>
    <p>One low fee per <span class="inline-highlight">month</span> fee with no lock-in contract. We guarantee that you will love our service!</p>
    <p class="fine-print">*Past results shown above isn't all that is guaranteed. 18+ only, responsible play required.</p>
  </div>
  <p class="site-url">www.kestrelvane.com.au</p>
</section>

</body>
</html>
```